Letterhead for a German Distribution/Manufacturing Company

We need a professional Letterhead in a unique Design.
not to playful.
The Letterhead has to show show that we are a international company with headquater in Germany.
all details like adress, Vat Tax Number, Bank Accout, Eori, email, Company number has to be on the Letterhead.
for example use: VAT TAX DE5470318 Bank Account: Kestrel Bank IBAN DE412058731ß204683 Swift: MORV0417352 EORI 3150428697 Company Number: HRB 51806 Adress: VOLMINTA UG Ahornweg 7 Postal Code 06384 City Lindenfeld Country: Germany Email: info@volminta-example.com
the design can be colored but doesnt have to be
Industry/Entity Type
Manufacturing and international distribution
Requirements
Must have
- show that we are a international company with headquater in Germany. our company infos and logo

```html
<!DOCTYPE html>
<html lang="de">
<head>
<meta charset="utf-8">
<title>VOLMINTA UG – Briefbogen</title>
<link rel="stylesheet" href="https://fonts.googleapis.com/css2?family=Figtree:wght@400;500;600&display=swap">
<style>
  :root {
    --backdrop: #e9e8e6;
    --paper-top: #ffffff;
    --paper-bottom: #f2f2f3;
    --ink: #2e2e30;
    --ink-soft: #4a4a4d;
    --band-start: #3c3c3f;
    --band-end: #1d1d1f;
    --band-text: #f4f4f4;
  }
  html, body {
    margin: 0;
    width: 1084px;
    height: 1200px;
    overflow: hidden;
    background: var(--backdrop);
    font-family: "Figtree", Arial, sans-serif;
  }
  .letterhead {
    position: absolute;
    left: 102px;
    top: 30px;
    width: 880px;
    height: 1140px;
    background: linear-gradient(180deg, var(--paper-top) 0%, var(--paper-bottom) 100%);
    box-shadow: 0 6px 22px rgba(0,0,0,0.18);
  }
  .brand {
    position: absolute;
    left: 62px;
    top: 58px;
    display: flex;
    align-items: center;
    gap: 14px;
  }
  .brand-dot {
    width: 62px;
    height: 62px;
    border-radius: 50%;
    background: var(--ink);
  }
  .brand-name {
    font-size: 40px;
    font-weight: 400;
    letter-spacing: 0.5px;
    color: var(--ink);
    line-height: 1;
  }
  .sender, .contact {
    position: absolute;
    top: 66px;
    font-size: 13px;
    line-height: 18px;
    color: var(--ink-soft);
    font-weight: 500;
  }
  .sender { left: 463px; }
  .contact { left: 655px; }
  .sender p, .contact p { margin: 0; }
  .contact p { display: flex; align-items: center; gap: 7px; }
  .contact svg { width: 11px; height: 11px; fill: var(--ink-soft); flex: none; }
  .legal-band {
    position: absolute;
    left: 0;
    bottom: 0;
    width: 100%;
    height: 67px;
    background: linear-gradient(90deg, var(--band-start), var(--band-end));
    color: var(--band-text);
    font-size: 13px;
    font-weight: 600;
    line-height: 19px;
    text-align: center;
    display: flex;
    flex-direction: column;
    justify-content: center;
  }
  .legal-band p { margin: 0; }
</style>
</head>
<body>
  <main class="letterhead">
    <header>
      <div class="brand">
        <span class="brand-dot"></span>
        <span class="brand-name">VOLMINTA</span>
      </div>
      <div class="sender">
        <p>VOLMINTA UG</p>
        <p>Ahornweg 7 06384</p>
        <p>City Lindenfeld Germany</p>
      </div>
      <div class="contact">
        <p>
          <svg viewBox="0 0 12 12" aria-hidden="true"><path d="M1 3.5C1 2 3 1 6 1s5 1 5 2.5v1H8.5V3.3H3.5v1.2H1z M2.5 5.5h7L11 11H1z"/></svg>
          730.512.4068
        </p>
        <p>
          <svg viewBox="0 0 12 12" aria-hidden="true"><path d="M0.5 2.5h11v7h-11z M1 3l5 3.5L11 3" stroke="#fff" stroke-width="0.9"/></svg>
          info@volminta-example.com
        </p>
        <p>
          <svg viewBox="0 0 12 12" aria-hidden="true"><circle cx="6" cy="6" r="5.5"/><path d="M3 4.5l2-1.5 1.5 1-1 2 1.5 1.5-.5 2.5-2-1.5-.5-2z M7.5 2.5l2 1-1 1.5z" fill="#fff"/></svg>
          www.volminta-example.com
        </p>
      </div>
    </header>
    <footer class="legal-band">
      <p>VAT TAX DE5470318 | Bank Account: Kestrel Bank IBAN DE412058731ß204683</p>
      <p>Swift: MORV0417352 EORI 3150428697 | Company Number: HRB 51806</p>
    </footer>
  </main>
</body>
</html>
```